New Vyro Strap Vs. Old Bulky Ankle Bracelets Comparison Chart

See vyro-link.com Need a cool high tech design that shows comparison between the New Vyro Strap and the Old Bulky embarrassing ankle bracelets.
list basic functions both devices perform then list all the great features the new vyro strap brings.
Features Both have
GPS TRACKING
GEO Fencing
EXECLUSION ZONES
INCLUSION ZONES
TAMPER ALERTS
FEATURES OF VYRO STRAP
Discrete wrist worn band no more embarrassing ankle bracelets
BIOMETRIC CHECK-INS VIA FACIAL
DYNAMIC REMOTE CHECK-INS
Monitoring Agencies and Enrollees are connected via frequent Video/Photo/Audio Check-ins. RECOGNITION VIDEO/PIC CHECKINS
GLIMPSECALL
VIDEO CONFERENCE WELFARE CHECKS ETC.
COMMUNICATION
COMPLIANCE ENFORCEMENT VIA TEXT VIDEO CHAT PHONE DYNAMIC REMOTE CHECK-INS
Monitoring Agencies and Enrollees are connected via frequent Video/Photo/Audio Check-ins.ñ

Target Market(s)

Courts,Attorneys,jails,probation and parole

Industry/Entity Type

electronic monitoring

Requirements
Must have
• Comparison of Vyro Strap and Ankle Bracelets
Nice to have
• High tech design

```html
<!DOCTYPE html>
<html lang="en">
<head>
<meta charset="utf-8">
<title>Vyro Strap vs. Old Bulky Ankle Bracelets</title>
<link href="https://fonts.googleapis.com/css2?family=Rubik:wght@300;400;500;700&display=swap" rel="stylesheet">
<style>
:root{
  --navy:#1d2f66;
  --navy-deep:#0a1a44;
  --ink:#1f1f24;
  --grey:#8a8d94;
  --grey-line:#c6c8cc;
  --tab-new:#d9e6f2;
  --tab-old:#efeff1;
  --page:#ffffff;
  --footer:#dce8f4;
}
*{box-sizing:border-box;margin:0;padding:0}
html,body{width:1200px;height:2966px;overflow:hidden;background:var(--page)}
body{position:relative;font-family:"Rubik",sans-serif;color:var(--ink)}
.sheet{position:absolute;left:107px;top:74px;width:986px;height:2788px;background:var(--page);box-shadow:0 18px 50px rgba(0,0,0,.28)}
.hero{position:absolute;left:0;top:0;width:986px;height:476px;overflow:hidden;
  background:radial-gradient(ellipse at 30% 35%,#2c4f9c 0%,#15306e 45%,var(--navy-deep) 100%)}
.hero-photo{position:absolute;inset:0;background:linear-gradient(120deg,rgba(255,255,255,0) 40%,rgba(200,210,230,.25) 60%,rgba(20,20,30,.55) 85%)}
.hero-cut{position:absolute;inset:0}
.brand{position:absolute;left:68px;top:72px;display:flex;align-items:center;gap:12px;color:#fff;font-weight:500;font-size:22px}
.brand-dot{width:26px;height:26px;border:3px solid #fff;border-radius:50%}
.hero-title{position:absolute;left:68px;top:232px;color:#fff;font-weight:500;font-size:41px}
.hero-sub{position:absolute;left:68px;top:294px;color:#fff;font-weight:400;font-size:31px;line-height:42px}
.compare-title{position:absolute;left:0;width:986px;top:514px;text-align:center;font-weight:500;font-size:41px}
.col-badge{position:absolute;top:610px;width:96px;height:96px;border-radius:50%;border:3px solid var(--navy);display:flex;align-items:center;justify-content:center}
.col-badge.old{border-color:var(--grey)}
.tab{position:absolute;top:712px;height:102px;display:flex;align-items:center;justify-content:center;text-align:center;font-weight:500;font-size:21px;line-height:28px}
.tab.new{left:65px;width:423px;background:var(--tab-new);color:var(--navy)}
.tab.old{left:488px;width:424px;background:var(--tab-old);color:var(--grey)}
.feature{position:absolute;width:430px;text-align:center;font-size:19px;font-weight:300;line-height:28px;color:var(--ink)}
.feature svg{display:block;margin:0 auto 6px;width:44px;height:44px;fill:none;stroke:var(--ink);stroke-width:2;stroke-linecap:round;stroke-linejoin:round}
.feature.left{left:62px}
.feature.right{left:486px}
.missing{position:absolute;left:682px;width:40px;height:40px}
.missing svg{width:40px;height:40px;fill:none;stroke:var(--grey-line);stroke-width:2}
.footer{position:absolute;left:0;top:2736px;width:986px;height:52px;background:var(--footer)}
.footer-web{position:absolute;left:340px;top:2722px;width:302px;height:66px;background:var(--navy)}
.footer-web svg{position:absolute;inset:0}
.footer-web span{position:absolute;inset:0;display:flex;align-items:center;justify-content:center;color:#fff;font-weight:500;font-size:24px}
.footer-mail,.footer-phone{position:absolute;top:2736px;height:52px;display:flex;align-items:center;gap:14px;font-size:23px}
.footer-mail{left:66px}
.footer-phone{left:670px;font-weight:700}
.footer svg{display:none}
.footer-mail svg,.footer-phone svg{width:28px;height:28px;fill:none;stroke:var(--ink);stroke-width:2.2;stroke-linejoin:round}
</style>
</head>
<body>
<div class="sheet">
  <section class="hero">
    <div class="hero-photo" role="img" aria-label="Dark blue technology network backdrop with a man in a suit wearing a black wrist monitoring band"></div>
    <svg class="hero-cut" width="986" height="476" viewBox="0 0 986 476"><polygon points="509,476 986,326 986,476" fill="#ffffff"/></svg>
    <div class="brand"><span class="brand-dot"></span>Vyro Strap</div>
    <h1 class="hero-title">Vyro Strap</h1>
    <p class="hero-sub">The Future of House Arrest<br>is worn on the wrist</p>
  </section>

  <h2 class="compare-title">Compare</h2>
  <div class="col-badge" style="left:229px"><svg width="52" height="52" viewBox="0 0 52 52" fill="none" stroke="#1d2f66" stroke-width="2.5"><rect x="6" y="18" width="24" height="16" rx="3"/><path d="M30 20h8a4 4 0 0 1 0 12h-8M14 22v8"/></svg></div>
  <div class="col-badge old" style="left:653px"><svg width="52" height="52" viewBox="0 0 52 52" fill="none" stroke="#8a8d94" stroke-width="2.5"><path d="M18 6v26l-8 8h28l-2-8-6-4V6"/><rect x="16" y="18" width="12" height="8" rx="2"/></svg></div>
  <div class="tab new">New<br>Vyro Strap</div>
  <div class="tab old">Old Bulky<br>Ankle Bracelets</div>

  <!-- shared features -->
  <div class="feature left" style="top:853px"><svg viewBox="0 0 44 44"><path d="M4 26h14l-6 6h12M28 4a7 7 0 0 1 7 7c0 6-7 13-7 13s-7-7-7-13a7 7 0 0 1 7-7z"/><circle cx="28" cy="11" r="2.5"/></svg>Gps Tracking</div>
  <div class="feature right" style="top:853px"><svg viewBox="0 0 44 44"><path d="M4 26h14l-6 6h12M28 4a7 7 0 0 1 7 7c0 6-7 13-7 13s-7-7-7-13a7 7 0 0 1 7-7z"/><circle cx="28" cy="11" r="2.5"/></svg>Gps Tracking</div>

  <div class="feature left" style="top:976px"><svg viewBox="0 0 44 44"><path d="M10 22 4 38h36l-6-16M22 6a6 6 0 0 1 6 6c0 5-6 12-6 12s-6-7-6-12a6 6 0 0 1 6-6z"/><circle cx="22" cy="12" r="2"/></svg>Geo Fencing</div>
  <div class="feature right" style="top:976px"><svg viewBox="0 0 44 44"><path d="M10 22 4 38h36l-6-16M22 6a6 6 0 0 1 6 6c0 5-6 12-6 12s-6-7-6-12a6 6 0 0 1 6-6z"/><circle cx="22" cy="12" r="2"/></svg>Geo Fencing</div>

  <div class="feature left" style="top:1099px"><svg viewBox="0 0 44 44"><path d="M22 6 40 38H4z M22 18v9M22 31v1"/></svg>Execlusion Zones</div>
  <div class="feature right" style="top:1099px"><svg viewBox="0 0 44 44"><path d="M22 6 40 38H4z M22 18v9M22 31v1"/></svg>Execlusion Zones</div>

  <div class="feature left" style="top:1222px"><svg viewBox="0 0 44 44"><path d="M22 4 38 10v12c0 9-7 15-16 18C13 37 6 31 6 22V10z M14 24l8-7 8 7M17 22v7h10v-7"/></svg>Inclusion Zones</div>
  <div class="feature right" style="top:1222px"><svg viewBox="0 0 44 44"><path d="M22 4 38 10v12c0 9-7 15-16 18C13 37 6 31 6 22V10z M14 24l8-7 8 7M17 22v7h10v-7"/></svg>Inclusion Zones</div>

  <div class="feature left" style="top:1345px"><svg viewBox="0 0 44 44"><path d="M10 32V20a12 12 0 0 1 24 0v12l3 3H7z M18 38h8M22 4v4"/></svg>Tamper Alerts</div>
  <div class="feature right" style="top:1345px"><svg viewBox="0 0 44 44"><path d="M10 32V20a12 12 0 0 1 24 0v12l3 3H7z M18 38h8M22 4v4"/></svg>Tamper Alerts</div>

  <!-- strap-only features -->
  <div class="feature left" style="top:1456px"><svg viewBox="0 0 44 60" style="height:60px"><path d="M12 22V8h20v14M12 42v12h20V42"/><rect x="8" y="22" width="28" height="20" rx="5"/><path d="M17 8v14M22 8v14M27 8v14"/></svg>Discrete Wrist Worn Band<br>No More Embarrassing Ankle Bracelets</div>
  <div class="missing" style="top:1468px"><svg viewBox="0 0 40 40"><rect x="2" y="2" width="36" height="36"/><path d="M12 12l16 16M28 12 12 28"/></svg></div>

  <div class="feature left" style="top:1619px"><svg viewBox="0 0 44 44"><path d="M4 12V4h8M32 4h8v8M40 32v8h-8M12 40H4v-8"/><circle cx="22" cy="17" r="6"/><path d="M11 34a11 11 0 0 1 22 0"/></svg>Biometric Check-ins Via Facial</div>
  <div class="missing" style="top:1630px"><svg viewBox="0 0 40 40"><rect x="2" y="2" width="36" height="36"/><path d="M12 12l16 16M28 12 12 28"/></svg></div>

  <div class="feature left" style="top:1742px"><svg viewBox="0 0 44 44"><circle cx="12" cy="22" r="5"/><circle cx="32" cy="10" r="5"/><circle cx="32" cy="34" r="5"/><path d="M16.5 19.5l11-7M16.5 24.5l11 7"/></svg>Dynamic Remote Check-ins</div>
  <div class="missing" style="top:1753px"><svg viewBox="0 0 40 40"><rect x="2" y="2" width="36" height="36"/><path d="M12 12l16 16M28 12 12 28"/></svg></div>

  <div class="feature left" style="top:1862px"><svg viewBox="0 0 44 44"><path d="M22 4l5.5 11.5 12.5 1.5-9.2 8.6 2.4 12.4L22 32l-11.2 6 2.4-12.4L4 17l12.5-1.5z"/></svg>Video Conference Welfare Checks Etc.</div>
  <div class="missing" style="top:1876px"><svg viewBox="0 0 40 40"><rect x="2" y="2" width="36" height="36"/><path d="M12 12l16 16M28 12 12 28"/></svg></div>

  <div class="feature left" style="top:1985px"><svg viewBox="0 0 44 44"><path d="M2 22s8-12 20-12 20 12 20 12-8 12-20 12S2 22 2 22z"/><circle cx="22" cy="22" r="6"/></svg>Monitoring Agencies And Enrollees Are Connected<br>Via Frequent Video/photo/audio Check-ins.<br>Recognition Video/pic Checkins</div>
  <div class="missing" style="top:1999px"><svg viewBox="0 0 40 40"><rect x="2" y="2" width="36" height="36"/><path d="M12 12l16 16M28 12 12 28"/></svg></div>

  <div class="feature left" style="top:2172px"><svg viewBox="0 0 44 44"><rect x="4" y="12" width="26" height="20" rx="2"/><path d="M30 19l10-6v18l-10-6"/></svg>Glimpsecall</div>
  <div class="missing" style="top:2183px"><svg viewBox="0 0 40 40"><rect x="2" y="2" width="36" height="36"/><path d="M12 12l16 16M28 12 12 28"/></svg></div>

  <div class="feature left" style="top:2295px"><svg viewBox="0 0 44 44"><path d="M9 5h8l3 9-5 3a22 22 0 0 0 12 12l3-5 9 3v8a3 3 0 0 1-3 3C18 38 6 26 6 8a3 3 0 0 1 3-3z"/></svg>Communication</div>
  <div class="missing" style="top:2306px"><svg viewBox="0 0 40 40"><rect x="2" y="2" width="36" height="36"/><path d="M12 12l16 16M28 12 12 28"/></svg></div>

  <div class="feature left" style="top:2418px"><svg viewBox="0 0 44 44"><path d="M14 6l12 12M8 12l12 12M11 9l12 12-6 6M23 21l16 16M4 40h16v-4H4z"/></svg>Compliance Enforcement Via Text Video Chat</div>
  <div class="missing" style="top:2429px"><svg viewBox="0 0 40 40"><rect x="2" y="2" width="36" height="36"/><path d="M12 12l16 16M28 12 12 28"/></svg></div>

  <div class="feature left" style="top:2538px"><svg viewBox="0 0 44 44"><path d="M22 8c10 0 18 6 18 13s-8 13-18 13c-2 0-4 0-6-1l-8 4 2-7c-4-2-6-6-6-9C4 14 12 8 22 8z"/><circle cx="15" cy="21" r="1.5"/><circle cx="22" cy="21" r="1.5"/><circle cx="29" cy="21" r="1.5"/></svg>Phone Dynamic Remote Check-ins</div>
  <div class="missing" style="top:2551px"><svg viewBox="0 0 40 40"><rect x="2" y="2" width="36" height="36"/><path d="M12 12l16 16M28 12 12 28"/></svg></div>

  <footer>
    <div class="footer"></div>
    <div class="footer-mail"><svg viewBox="0 0 28 28"><rect x="3" y="7" width="22" height="15"/><path d="M3 7l11 8 11-8"/></svg>info@vyro-link.com</div>
    <div class="footer-web"><svg width="302" height="66" viewBox="0 0 302 66"><polygon points="0,66 26,0 276,0 302,66" fill="#ffffff" opacity="0"/></svg><span>vyro-link.com</span></div>
    <div class="footer-phone"><svg viewBox="0 0 28 28"><circle cx="14" cy="14" r="12"/><path d="M10 8h3l1 4-2 1a7 7 0 0 0 3 3l1-2 4 1v3c-6 1-11-4-10-10z"/></svg>1-888-555-0142</div>
  </footer>
</div>
</body>
</html>
```